Business Card Design Project

We need a business card for a new technology services company. We develop software and implement software packages for our business customers and although we will begin with just one or two service offerings, our service offerings will expand over time. Our name comes from the an author, KL Barrow, and his "idea" was that opportunity should be based on ability and achievement, not on social status.

We would like to see a design that is standard in its size and shape, but stands apart in its dramatic color contrasts. The card should not use too many colors - the colors used in the background should highlight the brilliant blues of the logo (see attachment) to dramatic effect. The background should not be white.

If necessary, you can change the color of the words "KL Barrow", but not the word "Idea".

Card size should be U.S. standard 2 inches by 3.5 inches and provide for 1/8 inch bleed area on each side.

We need a design for both sides of the business card, one side communicating the company logo and contact information, the other side being purely graphical, incorporating the logo but no other information.

Contact Information Required:
Kate Brook
KateBrook@klbarrowvista.com
614-387-2259

Target Market(s)

Business executives

Industry/Entity Type

Software

Requirements
Must have
• It must have the full company logo on one side, and at least the graphic element of the logo on the other. Either that or the full logo on both.
Nice to have
• It would be nice to have a design that could work without needing two different textures. For example, it would be nice if the entire card could be shiny, not just parts of the card.

It would also be nice if texture is something we could add later.
Should not have
• The card should not use the color green.

```html
<!DOCTYPE html>
<html lang="en">
<head>
<meta charset="utf-8">
<title>Barrowvista — Business Card</title>
<link rel="stylesheet" href="https://fonts.googleapis.com/css2?family=Open+Sans:wght@400;700&display=swap">
<style>
  :root {
    --page: #ffffff;
    --card: #1f1f1f;
    --brand-blue: #0e9ad8;
    --brand-blue-deep: #0a7fc0;
    --brand-blue-bright: #12b2ee;
    --wordmark: #a8a8a8;
    --text-light: #f2f2f2;
    --card-shadow: rgba(0, 0, 0, 0.45);
  }
  * { margin: 0; padding: 0; box-sizing: border-box; }
  html, body {
    width: 1200px;
    height: 1000px;
    overflow: hidden;
    background: var(--page);
    font-family: "Open Sans", sans-serif;
  }
  .sheet {
    position: relative;
    width: 1200px;
    height: 1000px;
  }
  .card {
    position: absolute;
    left: 274px;
    width: 644px;
    height: 368px;
    border-radius: 22px;
    background: var(--card);
    box-shadow: 2px 5px 6px var(--card-shadow);
    overflow: hidden;
  }
  .card--front { top: 104px; }
  .card--back { top: 535px; }

  .wordmark {
    position: absolute;
    color: var(--wordmark);
    font-weight: 400;
    letter-spacing: -1.5px;
    white-space: nowrap;
    line-height: 1;
  }
  .brand-dot {
    position: absolute;
    border-radius: 50%;
    background: var(--brand-blue);
  }

  .card--front .brand-dot {
    left: 492px; top: 110px;
    width: 96px; height: 96px;
  }
  .card--front .wordmark {
    left: 44px; top: 272px;
    font-size: 52px;
  }
  .card--front .web {
    position: absolute;
    right: 302px; top: 322px;
    font-size: 15px;
    letter-spacing: 1.3px;
    color: var(--text-light);
  }

  .card--back .brand-dot {
    left: 520px; top: 52px;
    width: 64px; height: 64px;
  }
  .card--back .wordmark {
    left: 226px; top: 114px;
    font-size: 48px;
  }
  .contact {
    position: absolute;
    left: 46px; top: 223px;
    color: var(--text-light);
  }
  .contact__name {
    font-size: 22px;
    font-weight: 700;
    color: var(--brand-blue);
    margin-bottom: 18px;
    letter-spacing: 0.2px;
  }
  .contact__line {
    display: flex;
    align-items: center;
    gap: 9px;
    font-size: 15px;
    line-height: 22px;
  }
  .contact__icon { width: 16px; height: 16px; fill: var(--brand-blue); flex: none; }

  .web-band {
    position: absolute;
    left: 0; bottom: 0;
    width: 356px; height: 36px;
  }
  .web-band__label {
    position: absolute;
    left: 48px; bottom: 9px;
    font-size: 15px;
    letter-spacing: 1.3px;
    color: var(--text-light);
  }
</style>
</head>
<body>
<main class="sheet">

  <section class="card card--front" aria-label="Business card, front">
    <span class="brand-dot"></span>
    <div class="wordmark">Barrowvista</div>
    <div class="web">www.klbarrowvista.com</div>
  </section>

  <section class="card card--back" aria-label="Business card, back">
    <span class="brand-dot"></span>
    <div class="wordmark">Barrowvista</div>

    <div class="contact">
      <p class="contact__name">Kate Brook</p>
      <p class="contact__line">
        <svg class="contact__icon" viewBox="0 0 16 16" aria-hidden="true">
          <path d="M3.2 1.2l2.4-.4 1.5 3.4-1.6 1.2c.8 1.8 2.2 3.3 4 4.2l1.3-1.6 3.4 1.5-.4 2.5c-.2.9-1 1.4-1.9 1.3C6.7 12.7 3.1 9 2.5 3.8c-.1-1.2.2-2.3.7-2.6z"/>
        </svg>
        614-387-2259
      </p>
      <p class="contact__line">
        <svg class="contact__icon" viewBox="0 0 16 16" aria-hidden="true">
          <path d="M0 3h16v10H0zM1.2 4.2v.3L8 9l6.8-4.5v-.3zM1.2 6v5.8h13.6V6L8 10.5z"/>
        </svg>
        KateBrook@klbarrowvista.com
      </p>
    </div>

    <svg class="web-band" viewBox="0 0 356 36" aria-hidden="true">
      <defs>
        <linearGradient id="band-fill" x1="0" y1="0" x2="1" y2="0">
          <stop offset="0" stop-color="#0a7fc0"/>
          <stop offset="1" stop-color="#12b2ee"/>
        </linearGradient>
      </defs>
      <path d="M0 0H306C330 0 348 16 356 36H0Z" fill="url(#band-fill)"/>
    </svg>
    <div class="web-band__label">www.klbarrowvista.com</div>
  </section>

</main>
</body>
</html>
```